Business card for builder specialising in renovations.

Need a card for our building business. Business name is under Martin Powles.
Have licence number on card ( 527691K)
Contact number (0400 382 415)
Want to work on logo for some business cards and shirts - something with MP or MPB or open to ideas??
No animations, No hammers. Something sharp and eye catching.
Highlight that we are a renovation specialist. Simple on front with extra details on back with some lines to jot down things.

Target Market(s)

Renovators

Industry/Entity Type

Building

Contact Information for Business Card

2 sided with room on back to jot things down.
Extra details on back so front can be simple ..like, renovations, bathrooms, decks, extensions, new builds,

Logo Text

MP

Font styles to use
Serif

Requirements
Must have
• Eye catching design .
• Name : Martin powles
• Licence number
• Contact number - 0400382415
Nice to have
• Some logo design that we can carry through to other forms of advertising
• Local builder
• Quality work
Should not have
• No animations

```html
<!DOCTYPE html>
<html lang="en">
<head>
<meta charset="utf-8">
<title>Martin Powles — Business Card</title>
<link rel="stylesheet" href="https://fonts.googleapis.com/css2?family=Cormorant+Garamond:wght@400&family=Exo+2:ital,wght@1,400&display=swap">
<style>
  :root {
    --card-dark: #1a1d1f;
    --lime: #80ff00;
    --white: #ffffff;
    --ink: #111314;
  }
  * { margin: 0; padding: 0; box-sizing: border-box; }
  html, body {
    width: 1200px;
    height: 720px;
    overflow: hidden;
    background: var(--card-dark);
  }
  .card {
    position: relative;
    width: 1200px;
    height: 720px;
    background: var(--card-dark);
    overflow: hidden;
  }
  .brand {
    position: absolute;
    left: 60px;
    top: 60px;
    width: 420px;
    height: 540px;
    display: flex;
    align-items: center;
    justify-content: center;
  }
  .brand-name {
    font-family: "Cormorant Garamond", Georgia, serif;
    font-weight: 400;
    font-size: 54px;
    letter-spacing: 1px;
    color: var(--white);
    white-space: nowrap;
  }
  .divider {
    position: absolute;
    left: 522px;
    top: 94px;
    width: 3px;
    height: 506px;
    background: var(--lime);
  }
  .contact-row {
    position: absolute;
    left: 571px;
    display: flex;
    align-items: center;
    height: 100px;
  }
  .contact-row--name { top: 60px; }
  .contact-row--licence { top: 187px; }
  .contact-row--phone { top: 302px; }
  .contact-icon {
    width: 100px;
    height: 100px;
    flex: none;
  }
  .contact-text {
    margin-left: 65px;
    font-family: "Exo 2", Arial, sans-serif;
    font-style: italic;
    font-weight: 400;
    font-size: 31px;
    letter-spacing: 1px;
    color: var(--white);
    white-space: nowrap;
  }
  .notes-panel {
    position: absolute;
    left: 573px;
    top: 425px;
    width: 640px;
    height: 249px;
    background: var(--lime);
    border-radius: 7px;
  }
  .note-line {
    position: absolute;
    height: 3px;
    background: var(--white);
  }
  .note-line--1 { left: 25px; top: 36px; width: 581px; }
  .note-line--2 { left: 25px; top: 101px; width: 576px; }
  .note-line--3 { left: 30px; top: 169px; width: 568px; }
  .note-line--4 { left: 209px; top: 222px; width: 211px; }
  .base-band {
    position: absolute;
    left: 0;
    top: 702px;
    width: 1200px;
    height: 18px;
    background: var(--lime);
  }
</style>
</head>
<body>
  <main class="card">
    <section class="brand">
      <span class="brand-name">MARTIN POWLES</span>
    </section>

    <div class="divider"></div>

    <div class="contact-row contact-row--name">
      <svg class="contact-icon" viewBox="0 0 100 100" aria-hidden="true">
        <circle cx="50" cy="50" r="50" fill="var(--lime)"/>
        <circle cx="50" cy="50" r="34" fill="var(--ink)"/>
        <circle cx="50" cy="50" r="30" fill="none" stroke="var(--lime)" stroke-width="2"/>
        <ellipse cx="50" cy="42" rx="10" ry="12" fill="var(--lime)"/>
        <path d="M28 74 C30 60 40 56 50 56 C60 56 70 60 72 74 Z" fill="var(--lime)"/>
      </svg>
      <span class="contact-text">MARTIN POWLES</span>
    </div>

    <div class="contact-row contact-row--licence">
      <svg class="contact-icon" viewBox="0 0 100 100" aria-hidden="true">
        <circle cx="50" cy="50" r="50" fill="var(--lime)"/>
        <rect x="20" y="28" width="60" height="44" rx="5" fill="var(--ink)"/>
        <rect x="26" y="34" width="48" height="32" rx="2" fill="var(--lime)"/>
        <rect x="30" y="40" width="18" height="4" fill="var(--ink)"/>
        <rect x="30" y="48" width="18" height="4" fill="var(--ink)"/>
        <rect x="30" y="56" width="18" height="4" fill="var(--ink)"/>
        <rect x="53" y="39" width="17" height="22" fill="var(--ink)"/>
        <circle cx="61.5" cy="47" r="4" fill="var(--lime)"/>
        <path d="M55 60 C56 54 67 54 68 60 Z" fill="var(--lime)"/>
      </svg>
      <span class="contact-text">527691K</span>
    </div>

    <div class="contact-row contact-row--phone">
      <svg class="contact-icon" viewBox="0 0 100 100" aria-hidden="true">
        <circle cx="50" cy="50" r="50" fill="var(--lime)"/>
        <path d="M30 24 L40 22 L46 36 L39 42 C43 51 49 57 58 61 L64 54 L78 60 L76 70 C74 74 70 76 65 75 C45 71 29 55 25 35 C24 30 26 26 30 24 Z" fill="var(--ink)"/>
      </svg>
      <span class="contact-text">0400 382 415</span>
    </div>

    <section class="notes-panel" aria-label="Notes">
      <div class="note-line note-line--1"></div>
      <div class="note-line note-line--2"></div>
      <div class="note-line note-line--3"></div>
      <div class="note-line note-line--4"></div>
    </section>

    <div class="base-band"></div>
  </main>
</body>
</html>
```